Tiny Meadow Product Label for Tear-Free Head-to-Toe Wash

Need a bottle label design for a new line of natural products targeting infants and children. Products are Pediatrician-developed and paraben-free, sulfate-free, fragrance-free, and cruelty-free. Design should be clean and have a high-end feel to it. Will need other product labels in Tiny Meadow line designed as well in upcoming projects.

Target Market(s)

Newborn to young elementary age children and their parents

Industry/Entity Type

Cosmetics/Beauty

Font styles to use
Other font styles liked:
• Brand fonts are Jost and Sonorous

Colors

Designer to choose colors to be used in the design.

Requirements
Must have
• Tiny Meadow logo, Pediatrician Developed logo, and a clean high-end feel to it. The label must fit the specialty bottle we will be using (label measurements and diagram will be provided) for the front and back of bottle only (NOT the side labels). It must include our list of ingredients (will provide once designer selected).
Nice to have
• Should stand out on the shelf of other baby products due to it's clean simplicity and high-end feel
Should not have
• too much of a "kiddie" feel to it (targeting the parents not the kids)

```html
<!DOCTYPE html>
<html lang="en">
<head>
<meta charset="utf-8">
<title>Tiny Meadow – Tear-Free Head-to-Toe Wash Labels</title>
<link href="https://fonts.googleapis.com/css2?family=Archivo+Black&family=Jost:ital,wght@0,400;0,500;0,600;1,600;1,700&display=swap" rel="stylesheet">
<style>
  :root {
    --page: #ffffff;
    --label: #faf8f5;
    --gold: #9a7330;
    --ink: #222222;
    --body: #2e2e2e;
    --label-edge: #eee9e1;
  }
  * { box-sizing: border-box; margin: 0; padding: 0; }
  html, body { width: 1200px; height: 1200px; overflow: hidden; background: var(--page); }
  .canvas {
    width: 1200px; height: 1200px;
    display: flex; justify-content: center; align-items: center; gap: 64px;
  }
  .label {
    width: 340px; height: 500px;
    background: var(--label);
    border: 1px solid var(--label-edge);
    border-radius: 48% 48% 0 0 / 44px 44px 0 0;
    display: flex; flex-direction: column; align-items: center;
    font-family: "Jost", Arial, sans-serif;
    color: var(--body);
  }

  /* Front */
  .label--front { padding: 70px 24px 24px; }
  .brand { display: flex; align-items: center; gap: 12px; }
  .brand__mark {
    width: 52px; height: 52px; border-radius: 50%;
    border: 2px solid var(--gold);
  }
  .brand__name { font-family: "Jost", Arial, sans-serif; font-weight: 600; font-size: 22px; color: var(--ink); letter-spacing: 0.5px; }
  .product-title {
    margin-top: 44px;
    font-family: "Archivo Black", "Arial Black", sans-serif;
    font-size: 41px; line-height: 43px; text-align: center; color: var(--ink);
  }
  .tagline {
    margin-top: 14px;
    background: var(--gold); color: #fff;
    font-size: 15px; padding: 4px 22px; border-radius: 14px;
  }
  .claims { margin-top: 30px; display: flex; gap: 20px; }
  .claims__badge {
    width: 48px; height: 48px; border-radius: 50%;
    border: 1.5px solid var(--ink);
  }
  .net-weight { margin-top: auto; color: var(--gold); font-weight: 500; font-size: 15px; }

  /* Back */
  .label--back { padding: 22px 40px 20px; text-align: center; font-size: 13.5px; line-height: 17px; }
  .back-mark { width: 40px; height: 40px; border-radius: 50%; border: 1.5px solid var(--gold); margin-bottom: 16px; }
  .copy { text-align: justify; text-align-last: center; }
  .section-title {
    margin: 14px 0 6px;
    color: var(--gold); font-style: italic; font-weight: 700; font-size: 18px;
  }
  .maker { margin-top: auto; width: 100%; display: flex; justify-content: space-between; align-items: flex-end; text-align: left; }
  .maker__heading { color: var(--gold); font-style: italic; font-weight: 600; }
  .maker__seal { width: 56px; height: 56px; border-radius: 50%; border: 1.5px solid var(--gold); }
</style>
</head>
<body>
<main class="canvas">
  <section class="label label--front">
    <div class="brand">
      <span class="brand__mark"></span>
      <span class="brand__name">Tiny Meadow</span>
    </div>
    <h1 class="product-title">Tear-Free<br>Head-to-Toe<br>Wash</h1>
    <p class="tagline">Naturally formulated for delicate skin</p>
    <div class="claims" aria-label="Paraben free, sulfate free, fragrance free, cruelty free">
      <span class="claims__badge"></span>
      <span class="claims__badge"></span>
      <span class="claims__badge"></span>
      <span class="claims__badge"></span>
    </div>
    <p class="net-weight">Net wt: 73 mL/2,43 fl.oz</p>
  </section>

  <section class="label label--back">
    <span class="back-mark"></span>
    <p class="copy">A gentle, all-in-one cleanser made with natural ingredients to protect and nourish baby’s delicate hair and skin. Pediatrician-developed and suitable for daily use from newborn onwards.</p>
    <h2 class="section-title">Directions:</h2>
    <p class="copy">Dispense a small amount into hands or washcloth. Gently massage into wet hair and skin. Rinse thoroughly. Avoid contact with eyes.</p>
    <h2 class="section-title">Ingredients:</h2>
    <p class="copy">Aqua, Glycerin, Decyl Glucoside, Sodium Lauroyl Lactylate, Coco-Glucoside, Glyceryl Oleate, Xanthan Gum, Sodium Benzoate, Citric Acid. (Full list to be finalized.)</p>
    <div class="maker">
      <p><span class="maker__heading">Manufactured for</span><br>Tiny Meadow Co.<br>tinymeadow.com/Made in USA</p>
      <span class="maker__seal" aria-label="Pediatrician developed seal"></span>
    </div>
  </section>
</main>
</body>
</html>
```